K7 Construction Site Sign

I would like to get a sign designed which would be installed at a construction sign. I would like to incorporate my current logo, font and colors in the sign. The sign would be 30" x 60" (vertical). Would like to keep it clean and simple yet eye catching and sparks interest. I have attached my branding colors. I would like the background to be the branded blue with white text.

```html
<!DOCTYPE html>
<html lang="en">
<head>
<meta charset="utf-8">
<title>K7 Construction Site Sign</title>
<link href="https://fonts.googleapis.com/css2?family=Mulish:wght@400&display=swap" rel="stylesheet">
<style>
  :root {
    --brand-blue: #2a5185;
    --brand-blue-deep: #1d3d69;
    --brand-white: #ffffff;
    --page: #ffffff;
  }
  html, body {
    margin: 0;
    padding: 0;
    width: 1200px;
    height: 829px;
    overflow: hidden;
    background: var(--page);
  }
  .canvas {
    position: relative;
    width: 1200px;
    height: 829px;
  }
  .site-sign {
    position: absolute;
    left: 410px;
    top: 34px;
    width: 380px;
    height: 760px;
    display: block;
  }
  .sign-base { fill: var(--brand-blue); }
  .sign-edge { fill: url(#edge-shade); }
  .sign-wear { filter: url(#grunge); }
  .sign-text {
    fill: var(--brand-white);
    font-family: "Mulish", sans-serif;
    font-weight: 400;
  }
  .brand-name { font-size: 128px; letter-spacing: -3px; }
  .company-line { font-size: 50px; }
</style>
</head>
<body>
  <main class="canvas">
    <svg class="site-sign" viewBox="0 0 380 760" role="img" aria-label="K7 Building &amp; Renovation Ltd. site sign">
      <defs>
        <radialGradient id="edge-shade" cx="50%" cy="45%" r="75%">
          <stop offset="60%" stop-color="#1d3d69" stop-opacity="0"/>
          <stop offset="100%" stop-color="#1d3d69" stop-opacity="0.55"/>
        </radialGradient>
        <filter id="grunge" x="0" y="0" width="100%" height="100%">
          <feTurbulence type="fractalNoise" baseFrequency="0.035 0.05" numOctaves="5" seed="7" result="noise"/>
          <feColorMatrix in="noise" type="matrix"
            values="0 0 0 0 0.11
                    0 0 0 0 0.22
                    0 0 0 0 0.38
                    0 0 0 -2.4 1.5" result="blotches"/>
          <feTurbulence type="fractalNoise" baseFrequency="0.9" numOctaves="2" seed="3" result="grain"/>
          <feColorMatrix in="grain" type="matrix"
            values="0 0 0 0 0.55
                    0 0 0 0 0.68
                    0 0 0 0 0.85
                    0 0 0 -3 1.6" result="specks"/>
          <feMerge>
            <feMergeNode in="blotches"/>
            <feMergeNode in="specks"/>
          </feMerge>
        </filter>
      </defs>

      <rect class="sign-base" width="380" height="760"/>
      <rect class="sign-wear" width="380" height="760" opacity="0.55"/>
      <rect class="sign-edge" width="380" height="760"/>

      <g class="sign-content" transform="translate(0 760) rotate(-90)">
        <text class="sign-text brand-name" x="62" y="236">K7</text>
        <text class="sign-text company-line" x="222" y="173">BUILDING &amp;</text>
        <text class="sign-text company-line" x="222" y="236">RENOVATION LTD.</text>
      </g>
    </svg>
  </main>
</body>
</html>
```